Tiskoro

We need a business card for our company is a holding for different business all are different we try to have some air of relax and fun in our projects we add pictures of the office to give you an idea od the mood of the business

Business

```html
<!DOCTYPE html>
<html lang="en">
<head>
<meta charset="utf-8">
<title>Tiskoro — Business Card</title>
<link rel="stylesheet" href="https://fonts.googleapis.com/css2?family=Exo+2:wght@400;500;600;700&display=swap">
<style>
  :root {
    --brown: #6b4a2e;
    --yellow: #f6eb2f;
    --card: #ffffff;
    --stage: #e9e6e1;
    --ink: #5a3f27;
  }
  * { margin: 0; padding: 0; box-sizing: border-box; }
  html, body {
    width: 1200px; height: 900px; overflow: hidden;
    background: var(--stage);
    font-family: "Exo 2", sans-serif;
  }
  .stage {
    width: 1200px; height: 900px;
    display: flex; flex-direction: column; align-items: center; justify-content: center;
    gap: 40px;
  }
  .card {
    position: relative;
    width: 700px; height: 400px;
    background: var(--card);
    border-radius: 28px;
    overflow: hidden;
    box-shadow: 0 6px 18px rgba(0,0,0,0.12);
  }
  .card-waves { position: absolute; inset: 0; width: 100%; height: 100%; }
  .brand {
    position: absolute;
    display: flex; align-items: center; gap: 12px;
    color: var(--brown);
    font-weight: 700; letter-spacing: 0.5px;
  }
  .brand-square { width: 34px; height: 34px; background: var(--yellow); }
  .front .brand { left: 48px; top: 56px; font-size: 48px; }
  .front .brand-square { width: 42px; height: 42px; }
  .address {
    position: absolute; left: 48px; top: 226px;
    color: var(--ink); font-size: 21px; font-weight: 500; line-height: 1.35;
    letter-spacing: 0.6px;
  }
  .back .brand { left: 260px; top: 34px; font-size: 34px; }
  .person { position: absolute; right: 110px; top: 96px; text-align: right; }
  .person-name { color: var(--brown); font-size: 24px; font-weight: 600; letter-spacing: 1.5px; }
  .person-title { color: var(--ink); font-size: 14px; font-weight: 500; letter-spacing: 1.5px; }
  .contacts {
    position: absolute; right: 60px; top: 150px;
    list-style: none; text-align: right;
    color: var(--ink); font-size: 15px; letter-spacing: 0.8px;
  }
  .contacts li { display: flex; justify-content: flex-end; align-items: center; gap: 10px; height: 24px; }
  .contacts svg { width: 16px; height: 16px; fill: var(--ink); }
</style>
</head>
<body>
<main class="stage">

  <section class="card front">
    <svg class="card-waves" viewBox="0 0 700 400" aria-hidden="true">
      <path d="M150,292 C390,286 560,220 700,90 L700,140 C560,250 380,292 150,296 Z" fill="var(--yellow)"/>
      <path d="M0,300 C260,300 520,270 700,150 L700,400 L0,400 Z" fill="var(--brown)" stroke="#fff" stroke-width="4"/>
    </svg>
    <div class="brand"><span class="brand-square"></span>Tiskoro</div>
    <p class="address">041.12th floor,Plaza<br>Harbor Lane KTV</p>
  </section>

  <section class="card back">
    <svg class="card-waves" viewBox="0 0 700 400" aria-hidden="true">
      <path d="M40,398 C300,380 560,300 700,150 L700,195 C560,320 320,392 40,402 Z" fill="var(--yellow)"/>
      <path d="M120,400 C360,392 580,320 700,210 L700,400 Z" fill="var(--brown)" stroke="#fff" stroke-width="4"/>
    </svg>
    <div class="brand"><span class="brand-square"></span>Tiskoro</div>
    <div class="person">
      <p class="person-name">DANA ROVELLI</p>
      <p class="person-title">PRESIDENT</p>
    </div>
    <ul class="contacts">
      <li>012 345 6789 <svg viewBox="0 0 16 16"><path d="M3 1l3 3-1.5 2a9 9 0 0 0 5.5 5.5L12 10l3 3-2 2C7 15 1 9 1 3z"/></svg></li>
      <li>012 345 6789 <svg viewBox="0 0 16 16"><path d="M4 0h8v16H4zM5.5 2v10h5V2zM7 13h2v1.5H7z" fill-rule="evenodd"/></svg></li>
      <li>012 345 6789 <svg viewBox="0 0 16 16"><path d="M4 1h7v4H4zM1 6h14v8H1zM3 8h2v2H3zM7 8h2v2H7zM11 8h2v2h-2z" fill-rule="evenodd"/></svg></li>
      <li>name@email.com <svg viewBox="0 0 16 16"><path d="M1 3h14v10H1zM2 4l6 5 6-5z" fill-rule="evenodd"/></svg></li>
      <li>www.sitename.com <svg viewBox="0 0 16 16"><circle cx="8" cy="8" r="7" fill="none" stroke="var(--ink)" stroke-width="1.5"/><path d="M1 8h14M8 1c-3 4-3 10 0 14M8 1c3 4 3 10 0 14" fill="none" stroke="var(--ink)" stroke-width="1.2"/></svg></li>
    </ul>
  </section>

</main>
</body>
</html>
```